Covid 19 Exit Strategy one page brochure

I would like to design, and will need URGENT help, a brochure detailing a Covid 19 Exit Strategy plan. This brochure will need to be understood easily and the graphics inside should make it easy for people to understand without reading the entire text. This project is quite urgent and needs to be completed THIS WEEK - by Saturday may 16th at the latest. I am attaching two examples. I will provide the text.

```html
<!DOCTYPE html>
<html lang="en">
<head>
<meta charset="utf-8">
<title>General Requirements – Exit Strategy</title>
<link rel="stylesheet" href="https://fonts.googleapis.com/css2?family=Nunito+Sans:wght@400;600&display=swap">
<style>
  :root {
    --bg-deep: #041a20;
    --bg-mid: #0a3a45;
    --bg-glow: #0d5a6a;
    --teal: #1a8fa8;
    --teal-light: #3fb8d0;
    --teal-soft: rgba(40, 170, 200, 0.55);
    --heading-grey: #8d8f90;
    --text: #ffffff;
    --band: #0e6f83;
  }
  * { margin: 0; padding: 0; box-sizing: border-box; }
  html, body { width: 887px; height: 1200px; overflow: hidden; background: var(--bg-deep); }
  .brochure {
    position: relative;
    width: 887px;
    height: 1200px;
    overflow: hidden;
    font-family: "Nunito Sans", "Avenir Next", sans-serif;
    color: var(--text);
    background:
      radial-gradient(ellipse 340px 260px at 260px 560px, rgba(13, 90, 106, 0.75), transparent 70%),
      radial-gradient(ellipse 360px 300px at 720px 900px, rgba(13, 80, 95, 0.6), transparent 70%),
      radial-gradient(ellipse 300px 240px at 150px 1050px, rgba(10, 70, 82, 0.55), transparent 70%),
      linear-gradient(180deg, var(--bg-mid) 0%, var(--bg-deep) 55%, #06262d 100%);
  }
  .hero { position: absolute; left: 0; top: 0; width: 887px; height: 410px; }
  .heading {
    position: absolute;
    left: 37px;
    top: 306px;
    font-weight: 400;
    font-size: 43px;
    line-height: 51px;
    letter-spacing: -0.5px;
  }
  .heading .light { color: var(--heading-grey); display: block; }
  .heading .strong { color: var(--text); display: block; }
  .requirement {
    position: absolute;
    left: 0;
    width: 887px;
  }
  .requirement .icon {
    position: absolute;
    left: 62px;
    width: 60px;
    height: 60px;
  }
  .requirement p {
    position: absolute;
    left: 149px;
    right: 30px;
    font-size: 16.4px;
    line-height: 21px;
    letter-spacing: 0.1px;
  }
  .icon .line { fill: none; stroke: #fff; stroke-width: 2; stroke-linecap: round; stroke-linejoin: round; }
  .icon .fill { fill: #fff; }
  .icon .accent { fill: var(--teal-light); }
  .footer-band { position: absolute; left: 0; bottom: 0; width: 887px; height: 17px; background: var(--band); }
</style>
</head>
<body>
<main class="brochure">

  <svg class="hero" viewBox="0 0 887 410" xmlns="http://www.w3.org/2000/svg">
    <defs>
      <linearGradient id="photoTone" x1="0" y1="0" x2="1" y2="1">
        <stop offset="0" stop-color="#2f6b7c"/>
        <stop offset="0.55" stop-color="#5f8392"/>
        <stop offset="1" stop-color="#223c46"/>
      </linearGradient>
    </defs>
    <!-- diagonal bands -->
    <g stroke-linecap="round" fill="none">
      <line x1="-40" y1="-40" x2="218" y2="258" stroke="#0c4f5e" stroke-width="62"/>
      <line x1="60" y1="-60" x2="210" y2="130" stroke="var(--teal-soft)" stroke-width="44"/>
      <line x1="-60" y1="40" x2="70" y2="185" stroke="#12788e" stroke-width="38" opacity="0.8"/>
      <line x1="-60" y1="130" x2="0" y2="200" stroke="#12788e" stroke-width="30" opacity="0.7"/>
    </g>
    <!-- photo area -->
    <path d="M228,0 L442,330 Q526,440 612,350 L887,92 L887,0 Z" fill="url(#photoTone)"
          role="img" aria-label="Photo of a health worker wearing a surgical mask, with floating virus particles"/>
    <!-- rim -->
    <path d="M228,0 L446,338 Q526,452 616,356 L887,98" fill="none" stroke="var(--teal)" stroke-width="12" stroke-linecap="round"/>
    <path d="M887,92 L800,172 Q840,190 887,160 Z" fill="var(--teal-light)" opacity="0.7"/>
  </svg>

  <h1 class="heading"><span class="light">GENERAL</span><span class="strong">REQUIREMENTS:</span></h1>

  <section class="requirement" style="top:427px">
    <svg class="icon" style="top:0" viewBox="0 0 60 60"><path class="line" d="M2,2 H28 L38,12 V58 H2 Z M28,2 V12 H38 M8,14 H20 M8,22 H30 M8,30 H24 M8,48 l3,-6 3,6 3,-3"/><path class="line" d="M30,56 l4,-10 20,-20 6,6 -20,20 z"/></svg>
    <p style="top:0;left:154px">Single digit downward trend of documented cases within the past 14days.</p>
  </section>

  <section class="requirement" style="top:510px">
    <svg class="icon" style="top:2px" viewBox="0 0 60 60"><path class="line" d="M14,56 V12 H46 V56 M2,56 V30 H14 M46,30 H58 V56 M1,57 H59"/><circle class="line" cx="30" cy="6" r="4"/><rect class="accent" x="22" y="46" width="16" height="10"/><path class="line" d="M19,18 h22 M19,24 h22 M19,30 h22 M19,36 h22 M5,40 h5 M50,40 h5 M5,48 h5 M50,48 h5"/></svg>
    <p style="top:0">Hospitals and the health care system are capable of treating patients without operating on a crisis mode.</p>
  </section>

  <section class="requirement" style="top:585px">
    <svg class="icon" style="top:2px" viewBox="0 0 60 60"><circle class="line" cx="30" cy="34" r="26" stroke-dasharray="3 4"/><rect class="accent" x="22" y="6" width="10" height="26"/><path class="line" d="M22,2 h10 v30 h-10 z M27,32 v8 M40,24 a12,12 0 0 1 0,24 M12,58 H48 V54 H12 Z M20,54 V48 H42"/><circle class="line" cx="34" cy="22" r="4"/></svg>
    <p style="top:0">Ability to screen and test symptomatic individuals within 24 hours of identification. Increased and sufficient testing capacity, to test at least 50% of all population if necessary within a timeframe of 3 months.</p>
  </section>

  <section class="requirement" style="top:679px">
    <svg class="icon" style="top:4px" viewBox="0 0 60 60"><rect class="line" x="2" y="6" width="30" height="34" rx="4"/><path class="line" d="M12,6 V2 H22 V6 M17,40 V60 M10,40 V50 H24 V40 M32,30 Q38,20 44,30 V56 Q40,62 36,56 M52,18 V40 M48,26 H56 V36 H48 Z"/><rect class="accent" x="7" y="14" width="20" height="12"/><path class="line" d="M11,20 h12 M15,17 v6"/></svg>
    <p style="top:0">Ability to surge ICU capacity on a short notice - 24h.</p>
  </section>

  <section class="requirement" style="top:767px">
    <svg class="icon" style="top:2px" viewBox="0 0 60 60"><circle class="accent" cx="30" cy="18" r="16"/><path d="M30,10 v16 M22,18 h16" stroke="#fff" stroke-width="4"/><path class="line" d="M14,30 Q2,34 10,38 H56 Q62,44 50,48 M2,44 H46 V60 H2 Z"/><path class="line" d="M7,50 h34 M7,55 h34" stroke-dasharray="3 2"/></svg>
    <p style="top:0">Ability to track and trace infected patients and contacts on a live basis and across the country and ability to react quickly to any unusual trends or outbreaks.</p>
  </section>

  <section class="requirement" style="top:856px">
    <svg class="icon" style="top:0" viewBox="0 0 60 72"><path class="line" d="M12,16 Q30,4 48,16 V22 H12 Z M26,12 h8 M30,8 v8"/><circle class="line" cx="30" cy="34" r="14"/><path class="line" d="M4,72 V62 Q6,52 20,50 L30,58 L40,50 Q54,52 56,62 V72"/><rect class="accent" x="24" y="60" width="12" height="12"/></svg>
    <p style="top:0;left:154px">Plan in place to trigger targeted or full-scale containment in case of sudden outbreaks</p>
  </section>

  <section class="requirement" style="top:950px">
    <svg class="icon" style="top:-2px" viewBox="0 0 60 60"><path class="line" d="M4,52 Q0,44 10,34 L40,8 Q52,2 56,12 Q58,22 46,34 L20,56 Q10,60 4,52 Z M14,34 L44,54 M22,28 L50,44 M10,44 L30,58 M54,10 Q60,4 56,2"/></svg>
    <p style="top:0">Mandatory use of masks (at least surgical grade) for everyone in all public areas and at work. Mandatory use of N95, or equivalent, masks for all healthcare front workers and for all government agencies and authorities that are involved in overseeing the containment activities.</p>
  </section>

  <section class="requirement" style="top:1046px">
    <svg class="icon" style="top:-8px" viewBox="0 0 60 60"><path class="line" d="M30,2 Q20,4 22,24 Q26,36 36,36 Q46,36 50,24 Q52,4 42,2 M36,36 V46 Q36,58 24,58 Q14,58 14,48 V44"/><circle class="line" cx="10" cy="46" r="6"/></svg>
    <p style="top:0">Mandatory daily checks of body temperature for everyone at the workplace or entering public areas.</p>
  </section>

  <section class="requirement" style="top:1118px">
    <svg class="icon" style="top:-3px" viewBox="0 0 60 60"><path class="line" d="M26,2 h8 l2,8 6,3 7,-4 6,6 -4,7 3,6 8,2 v8 l-8,2 -3,6 4,7 -6,6 -7,-4 -6,3 -2,8 h-8 l-2,-8 -6,-3 -7,4 -6,-6 4,-7 -3,-6 -8,-2 v-8 l8,-2 3,-6 -4,-7 6,-6 7,4 6,-3 z"/><circle class="accent" cx="30" cy="30" r="12"/><circle class="line" cx="30" cy="30" r="15"/><path d="M30,23 v14 M23,30 h14" stroke="#fff" stroke-width="4"/></svg>
    <p style="top:0">Mandatory sanitation in all places - use of disinfection available on a large scale.</p>
  </section>

  <div class="footer-band"></div>
</main>
</body>
</html>
```